The Neighbors Together Project

For submission to Lantern Campaign 2024
Need both Color and Black and White Versions
TITLE The Neighbors Together Project
Slogan; "Neighbors Together, one road...one Heart, just a different stride" -JT Pellow copyrights
Logo in Color and Logo in Black and White
Back of flyer will be The Field of Quiet Lanterns poem -JT Pellow
VOTE BLUE 2024 Header or Footer

I just want to thank you all for your participation in The Neighbors Together Project. In the next few days I will be reducing the choices down to 10. Id like for all of you to know Ive enjoyed seeing so many options and views on the Flyer. Mainly, I wanted to say to those who don't make the cut that I appreciate the work you've done.

LM Dorsey

```html
<!DOCTYPE html>
<html lang="en">
<head>
<meta charset="utf-8">
<title>Field of Quiet Lanterns — JT Pellow</title>
<link href="https://fonts.googleapis.com/css2?family=Anton&family=Jost:wght@500;600&display=swap" rel="stylesheet">
<style>
  :root {
    --paper: #fefefe;
    --ink: #0a0a0a;
    --backdrop-mid: #e8e8e8;
    --backdrop-light: #f3f3f3;
  }
  * { margin: 0; padding: 0; box-sizing: border-box; }
  html, body {
    width: 848px;
    height: 1200px;
    overflow: hidden;
    background: var(--paper);
  }
  .poem-sheet {
    position: relative;
    width: 848px;
    height: 1200px;
    background: var(--paper);
    color: var(--ink);
    overflow: hidden;
  }
  .backdrop-figure {
    position: absolute;
    left: -40px;
    top: 100px;
    width: 640px;
    height: 1100px;
    background: radial-gradient(closest-side at 45% 50%, var(--backdrop-mid) 0%, var(--backdrop-light) 55%, rgba(254,254,254,0) 100%);
  }
  .poem-title {
    position: absolute;
    top: 183px;
    left: 0;
    width: 848px;
    text-align: center;
    font-family: "Anton", sans-serif;
    font-weight: 400;
    font-size: 66px;
    line-height: 1;
    letter-spacing: 0.5px;
    text-transform: uppercase;
  }
  .poem-byline {
    position: absolute;
    top: 252px;
    left: 0;
    width: 848px;
    text-align: center;
    font-family: "Jost", sans-serif;
    font-weight: 600;
    font-size: 30px;
    line-height: 43px;
    letter-spacing: 1px;
    text-transform: uppercase;
  }
  .stanza {
    position: absolute;
    left: 0;
    width: 848px;
    text-align: center;
    white-space: nowrap;
    font-family: "Jost", sans-serif;
    font-weight: 500;
    font-size: 27px;
    line-height: 35px;
  }
  .stanza-1 { top: 310px; }
  .stanza-2 { top: 416px; }
  .stanza-3 { top: 559px; }
  .stanza-4 { top: 700px; }
  .stanza-5 { top: 841px; }
  .project-url {
    position: absolute;
    top: 978px;
    left: 0;
    width: 848px;
    text-align: center;
    font-family: "Jost", sans-serif;
    font-weight: 500;
    font-size: 26px;
    line-height: 35px;
    letter-spacing: 0.3px;
    text-transform: uppercase;
  }
</style>
</head>
<body>
<main class="poem-sheet">
  <div class="backdrop-figure" role="img" aria-label="Faint grey illustration of a torch-bearing monument figure in the background"></div>

  <h1 class="poem-title">Field of Quiet Lanterns</h1>
  <p class="poem-byline">By JT Pellow</p>

  <p class="stanza stanza-1">From porch lights down to lantern strings and candles in<br>the dusk,forever walking homeward in a glow of shared trust.</p>
  <p class="stanza stanza-2">We are a field of quiet lanterns...amber, silver, blue and<br>gold,forever walking homeward with a story to be<br>told.</p>
  <p class="stanza stanza-3">We have gathered in the meadow, lit a flame for every<br>door. Lending hands and open tables...always room for<br>more.</p>
  <p class="stanza stanza-4">Kind to strangers, Kind to neighbors, Kind at dusk or<br>dawn...sharing, caring all as kinfolk on the path we walk<br>along.</p>
  <p class="stanza stanza-5">We must always hold the lantern, keep the little flame<br>alight.<br>For together we are brighter on the darkest winter night.</p>

  <p class="project-url">www.neighborstogetherproject.org</p>
</main>
</body>
</html>
```